Marlowe Group needs a business card

I would like the card to be simple but modern and elegant.
I like black and white.
or black and gold.
we are a private finance lender and also are involved in property and property developments.

please look at the business card photos i provided i would like M.G only one one side and all the other details on the other side use fonts that tie in with my theme.

Industry/Entity Type

Finance

Contact Information for Business Card

Marlowe Group (M.G) Daniel Marlowe M: 0413586207 E: danmarl@inboxmail.test

Font styles to use
Other font styles liked:
• Use fonts that would reflect our business

Colors
000000
ffffff

Requirements
Must have
• one side of details
• other side has either M.G or Marlowe Group like in the photos provided

```html
<!DOCTYPE html>
<html lang="en">
<head>
<meta charset="utf-8">
<title>Marlowe Group – Business Card</title>
<link rel="stylesheet" href="https://fonts.googleapis.com/css2?family=Open+Sans:ital,wght@0,400;0,600;0,700;1,400&display=swap">
<style>
  :root {
    --backdrop: #e8e5e0;
    --card-white: #ffffff;
    --card-black: #0b0b0b;
    --pattern-dark: #151515;
    --gold: #d3a026;
    --ink: #3a3a3a;
    --black: #000000;
  }
  * { margin: 0; padding: 0; box-sizing: border-box; }
  html, body {
    width: 1200px;
    height: 987px;
    overflow: hidden;
    background: var(--backdrop);
    font-family: "Open Sans", Arial, sans-serif;
  }
  .canvas { position: relative; width: 1200px; height: 987px; }
  .card {
    position: absolute;
    left: 292px;
    width: 616px;
    height: 350px;
    box-shadow: 0 3px 10px rgba(0,0,0,0.25);
    overflow: hidden;
  }
  .card-front { top: 130px; background: var(--card-white); }
  .card-back { top: 506px; background: var(--card-black); }

  .brand-name {
    position: absolute;
    left: 28px;
    top: 46px;
    font-weight: 700;
    font-size: 30px;
    letter-spacing: 0.5px;
    color: var(--gold);
    text-transform: uppercase;
    line-height: 1;
  }

  .contact {
    position: absolute;
    right: 31px;
    top: 226px;
    text-align: right;
    color: var(--ink);
  }
  .contact-name {
    font-weight: 600;
    font-size: 23px;
    color: var(--gold);
    line-height: 1.2;
    margin-bottom: 6px;
  }
  .contact-line { font-size: 16px; line-height: 24px; }
  .contact-label { color: var(--gold); font-weight: 600; }

  .footer-band { position: absolute; left: 0; top: 314px; width: 616px; height: 36px; }
  .website {
    position: absolute;
    right: 31px;
    top: 318px;
    font-style: italic;
    font-size: 16px;
    color: var(--card-white);
    letter-spacing: 0.3px;
  }

  .back-pattern {
    position: absolute;
    inset: 0;
    background: linear-gradient(135deg, var(--pattern-dark), var(--card-black) 50%, var(--pattern-dark));
  }
  .monogram {
    position: absolute;
    left: 0;
    right: 0;
    top: 50%;
    transform: translateY(-50%);
    text-align: center;
    font-weight: 700;
    font-size: 108px;
    line-height: 1;
    letter-spacing: 4px;
    color: var(--gold);
  }
</style>
</head>
<body>
<main class="canvas">
  <section class="card card-front" aria-label="Card front">
    <div class="brand-name">Marlowe Group</div>

    <div class="contact">
      <p class="contact-name">Daniel Marlowe</p>
      <p class="contact-line"><span class="contact-label">Cell :</span> 0413586207</p>
      <p class="contact-line">danmarl@inboxmail.test</p>
    </div>

    <svg class="footer-band" viewBox="0 0 616 36" aria-hidden="true">
      <polygon points="0,15 340,15 334,21 0,21" fill="var(--gold)"/>
      <polygon points="346,21 366,0 616,0 616,36 0,36 0,27 338,27" fill="var(--black)"/>
    </svg>
    <p class="website">www.marlowegroup.test</p>
  </section>

  <section class="card card-back" aria-label="Card back">
    <div class="back-pattern" role="img" aria-label="Faint repeating diagonal monogram pattern on black"></div>
    <p class="monogram">M.G</p>
  </section>
</main>
</body>
</html>
```